Road Construction Company needs business cards

We would like a new business card designed for our business.

We're a road construction company based in Qld, Australia.

Can the business card please have the following information on it.

Name: Warren Halbeck
Position: General Manager
Phone: 0472 915 348
Email: Warren.halbeck@tovrin.com.au
Address: 87 Marrow Ave, Pendlebay, QLD, 4023
Website: www.tovrin.com.au

Visually we'd like the card to be professional and simple.

Attached is our logo.

Our website is www.tovrin.com.au

Target Market(s)

Men aged 25-60

Contact Information for Business Card

As listed in project description

Font styles to use
Serif

Requirements
Must have
• Large logo on back of card

```html
<!DOCTYPE html>
<html lang="en">
<head>
<meta charset="utf-8">
<title>Tovrin Business Card</title>
<link href="https://fonts.googleapis.com/css2?family=Saira:wght@400;700;800&display=swap" rel="stylesheet">
<style>
  :root {
    --backdrop: #2b2b2b;
    --card-white: #ffffff;
    --brand-blue: #0a56a6;
    --brand-deep: #063d78;
    --accent-blue: #2b93d8;
    --ink: #1b1b1b;
    --divider: #b9b9b9;
    --card-back: #0457a5;
  }
  * { margin: 0; padding: 0; box-sizing: border-box; }
  html, body {
    width: 1093px; height: 1200px; overflow: hidden;
    background: var(--backdrop);
    font-family: "Saira", sans-serif;
  }
  .canvas { position: relative; width: 1093px; height: 1200px; }
  .card {
    position: absolute; left: 265px; width: 578px; height: 356px;
    border-radius: 27px;
    box-shadow: 3px 4px 6px rgba(0,0,0,.55);
  }
  .card-front { top: 226px; background: var(--card-white); }
  .card-back { top: 621px; width: 581px; background: var(--card-back); }

  .front-logo {
    position: absolute; left: 33px; top: 154px; width: 224px;
    text-align: center;
    font-weight: 800; font-size: 44px; letter-spacing: 2px; line-height: 1;
    color: var(--brand-blue);
  }
  .divider {
    position: absolute; left: 278px; top: 75px; width: 1px; height: 208px;
    background: var(--divider);
  }
  .details { position: absolute; left: 301px; top: 90px; color: var(--ink); }
  .person-name {
    font-weight: 800; font-size: 18px; letter-spacing: 1.2px; line-height: 1;
    text-transform: uppercase; color: var(--brand-blue);
  }
  .person-role {
    font-size: 16px; line-height: 1; margin-top: 4px; color: var(--accent-blue);
  }
  .contact-list { list-style: none; margin-top: 16px; }
  .contact-list li {
    display: flex; align-items: center; gap: 6px;
    font-size: 16px; line-height: 21px;
  }
  .contact-list svg { width: 16px; height: 16px; flex: none; }
  .web-highlight { color: var(--brand-blue); }
  .address { margin-top: 12px; font-size: 16px; line-height: 21px; }

  .back-logo {
    position: absolute; left: 0; right: 0; top: 142px;
    text-align: center;
    font-weight: 800; font-size: 72px; letter-spacing: 6px; line-height: 1;
    color: var(--brand-deep);
  }
</style>
</head>
<body>
<main class="canvas">
  <section class="card card-front">
    <div class="front-logo">TOVRIN</div>
    <div class="divider"></div>
    <div class="details">
      <h1 class="person-name">Warren Halbeck</h1>
      <p class="person-role">General Manager</p>
      <ul class="contact-list">
        <li>
          <svg viewBox="0 0 16 16" aria-hidden="true"><path d="M3.5 1.5l2.3 2.6-1.3 1.8c.9 2 2.6 3.7 4.6 4.6l1.8-1.3 2.6 2.3-1.5 2.2C7 13.3 2.7 9 1.3 3z" fill="var(--brand-blue)"/><path d="M9.5 3.2a3.6 3.6 0 0 1 3.3 3.3M9.8 .8a6 6 0 0 1 5.4 5.4" stroke="var(--brand-blue)" stroke-width="1.3" fill="none"/></svg>
          0472 915 348
        </li>
        <li>
          <svg viewBox="0 0 16 16" aria-hidden="true"><rect x="0.5" y="3" width="15" height="10" fill="var(--brand-blue)"/><path d="M1 3.5l7 5.5 7-5.5M1 12.5l5-4.5M15 12.5l-5-4.5" stroke="#fff" stroke-width="1" fill="none"/></svg>
          Warren.halbeck@tovrin.com.au
        </li>
        <li>
          <svg viewBox="0 0 16 16" aria-hidden="true" fill="none" stroke="var(--brand-blue)" stroke-width="1.2"><circle cx="8" cy="8" r="6.8"/><ellipse cx="8" cy="8" rx="3" ry="6.8"/><path d="M1.2 8h13.6M2.3 4.5h11.4M2.3 11.5h11.4M8 1.2v13.6"/></svg>
          <span>www.<span class="web-highlight">tovrin</span>.com.au</span>
        </li>
      </ul>
      <p class="address">87 Marrow Ave<br>Pendlebay, QLD, 4023</p>
    </div>
  </section>

  <section class="card card-back">
    <div class="back-logo">TOVRIN</div>
  </section>
</main>
</body>
</html>
```